ReelBloom business card

We are a performing arts company providing training (to both kids and adults) as well as performers for events. We hope to bring joy and confidence on stage to the people we train, as well as joy to the audience when our artistes perform. Designs should convey the joy, confidence and vibrancy on stage. Design business card using the attached logo. Card to include name, mobile tel, email address, company address, and website. Double sided. To also include the following list of what the company does:
• Training & Enrichment
• Private & Corporate Entertainment
- Music composition & production

Industry/Entity Type

Training

Contact Information for Business Card

Card to include name, mobile tel, email address, company address, and website. Double sided. To also include the following list of what the company does:
• Training & Enrichment

Requirements
Nice to have
• Card need not be the traditional rectangular in shape but not too outrageous.

```html
<!DOCTYPE html>
<html lang="en">
<head>
<meta charset="utf-8">
<title>ReelBloom business card</title>
<link rel="stylesheet" href="https://fonts.googleapis.com/css2?family=Arimo:ital,wght@0,400;0,700;1,400&family=Tinos:wght@700&display=swap">
<style>
  :root {
    --bg: #e6e7ea;
    --card: #ffffff;
    --navy: #1f2f7a;
    --red: #d8202a;
    --brand: #e2334f;
    --watermark-a: #dcdde0;
    --watermark-b: #eeeff1;
  }
  * { box-sizing: border-box; margin: 0; padding: 0; }
  html, body { width: 1200px; height: 960px; overflow: hidden; }
  body {
    background: var(--bg);
    font-family: "Arimo", Arial, sans-serif;
    color: var(--navy);
    position: relative;
  }
  .card {
    position: absolute;
    top: 140px;
    width: 420px;
    height: 680px;
    background: var(--card);
    border-radius: 28px;
    box-shadow: 0 10px 30px rgba(0,0,0,.15), 0 2px 4px rgba(0,0,0,.08);
    overflow: hidden;
  }
  .card--front { left: 150px; }
  .card--back { left: 630px; }

  .music-decoration {
    position: absolute;
    left: 40px;
    width: 320px;
    height: 330px;
    border-radius: 50%;
    background: radial-gradient(circle at 50% 50%, var(--watermark-a), var(--watermark-b) 70%, transparent 72%);
    opacity: .8;
  }
  .card--front .music-decoration { top: 300px; }
  .card--back .music-decoration { top: 270px; }

  .brand {
    position: absolute;
    top: 70px;
    left: 0;
    right: 0;
    text-align: center;
  }
  .brand__row {
    display: inline-flex;
    align-items: center;
    gap: 12px;
  }
  .brand__dot {
    width: 22px;
    height: 22px;
    border-radius: 50%;
    background: var(--brand);
  }
  .brand__name {
    font-weight: 700;
    font-size: 54px;
    color: var(--brand);
    letter-spacing: -1px;
  }
  .brand__tagline {
    margin-top: 6px;
    font-size: 21px;
    color: var(--navy);
    letter-spacing: .5px;
  }

  .person {
    position: absolute;
    top: 250px;
    left: 46px;
  }
  .person__name {
    font-family: "Tinos", "Times New Roman", serif;
    font-weight: 700;
    font-size: 32px;
    color: var(--red);
  }
  .person__role {
    font-size: 16px;
    color: var(--navy);
    margin-top: 2px;
  }

  .contacts {
    position: absolute;
    top: 360px;
    left: 46px;
    right: 30px;
    list-style: none;
  }
  .contacts__item {
    display: flex;
    align-items: flex-start;
    gap: 14px;
    font-size: 20px;
    line-height: 1.2;
    margin-bottom: 14px;
    color: var(--navy);
  }
  .contacts__icon {
    flex: 0 0 20px;
    width: 20px;
    height: 20px;
    margin-top: 2px;
  }

  .services {
    position: absolute;
    top: 300px;
    left: 46px;
    right: 24px;
  }
  .services__title {
    font-family: "Tinos", "Times New Roman", serif;
    font-weight: 700;
    font-size: 32px;
    color: var(--red);
    margin-bottom: 22px;
  }
  .services__list { list-style: none; }
  .services__item {
    display: flex;
    gap: 12px;
    font-size: 20px;
    line-height: 1.25;
    margin-bottom: 12px;
    color: var(--navy);
    white-space: nowrap;
  }
  .services__bullet { color: var(--red); font-weight: 700; }
</style>
</head>
<body>

<section class="card card--front" aria-label="Business card front">
  <div class="music-decoration" role="img" aria-label="Faint grey treble clef with music notes and staff lines"></div>

  <div class="brand">
    <div class="brand__row">
      <span class="brand__name">ReelBloom</span>
      <span class="brand__dot"></span>
    </div>
    <p class="brand__tagline">blooming on every stage</p>
  </div>

  <div class="person">
    <h1 class="person__name">Employee name</h1>
    <p class="person__role">Managing Director</p>
  </div>

  <ul class="contacts">
    <li class="contacts__item">
      <svg class="contacts__icon" viewBox="0 0 20 20" aria-hidden="true"><path d="M5 2l3 4-2 2c1 2 3 4 5 5l2-2 4 3-2 3C9 17 3 11 2 5z" fill="#d8202a"/></svg>
      <span>455-7120 4388</span>
    </li>
    <li class="contacts__item">
      <svg class="contacts__icon" viewBox="0 0 20 20" aria-hidden="true"><rect x="5" y="2" width="10" height="16" rx="2" fill="none" stroke="#d8202a" stroke-width="2"/></svg>
      <span>035-6180 9472</span>
    </li>
    <li class="contacts__item">
      <svg class="contacts__icon" viewBox="0 0 20 20" aria-hidden="true"><rect x="2" y="4" width="16" height="12" fill="#d8202a"/><path d="M2 4l8 7 8-7" fill="none" stroke="#fff" stroke-width="1.5"/></svg>
      <span>hello@reelbloom.com</span>
    </li>
    <li class="contacts__item">
      <svg class="contacts__icon" viewBox="0 0 20 20" aria-hidden="true"><circle cx="10" cy="10" r="8" fill="#d8202a"/><path d="M2 10h16M10 2c-4 4-4 12 0 16M10 2c4 4 4 12 0 16" fill="none" stroke="#fff" stroke-width="1.2"/></svg>
      <span>www.reelbloom.com</span>
    </li>
    <li class="contacts__item">
      <svg class="contacts__icon" viewBox="0 0 20 20" aria-hidden="true"><path d="M10 1a6 6 0 0 0-6 6c0 5 6 12 6 12s6-7 6-12a6 6 0 0 0-6-6z" fill="#d8202a"/><circle cx="10" cy="7" r="2.2" fill="#fff"/></svg>
      <span>Your Address Inc 2nd Lane Ave Brookfield, NJ 00000</span>
    </li>
  </ul>
</section>

<section class="card card--back" aria-label="Business card back">
  <div class="music-decoration" role="img" aria-label="Faint grey treble clef with music notes and staff lines"></div>

  <div class="brand">
    <div class="brand__row">
      <span class="brand__name">ReelBloom</span>
      <span class="brand__dot"></span>
    </div>
    <p class="brand__tagline">blooming on every stage</p>
  </div>

  <div class="services">
    <h2 class="services__title">Service :-</h2>
    <ul class="services__list">
      <li class="services__item"><span class="services__bullet">*</span><span>Training &amp; Enrichment</span></li>
      <li class="services__item"><span class="services__bullet">*</span><span>Private &amp; Corporate Entertainment</span></li>
      <li class="services__item"><span class="services__bullet">*</span><span>Music composition &amp; production</span></li>
    </ul>
  </div>
</section>

</body>
</html>
```